Company Flyer for Electric boating company

I am looking for a company flyer which we can hand over to boat owners in the Netherlands (Amsterdam area). Our core business is to rebuild every boat (from 4 to 10 meters) into an electrically propelled boat. We are taking out diesels and replace them with a high quality electrical motor, inboard varying from 30 till 80 pk (hp). And outboard from 1pk (hp) till 200pk. We are the best, not the cheapest, not the most expensive. We only work with the best materials. The flyer has to be sort of in line with our website and branding.

Major advantages of electric boating are:
- completely silent
- no fumes, smells or smoke
- cheap to operate
- environmentally friendly
- obliged in more and more areas
- no maintenance
- more enjoyable

The flyer should be A5 format. Since all the text has to be in Dutch I expect only the graphical design and layout for advantages, process, pricing and contact details etc.

Target Market(s)

Boat owners in the Netherlands

Font styles to use
Sans Serif

Colors
9bcb3c
add136
cadf82
0555a3
3176b5
85acd3
e0ebf3

Requirements
Must have
• Clean design, in line with website: www.volthaven.nl
Nice to have
• icons for advantages, boating etc

2 sides
Should not have
• Steering wheel...

```html
<!DOCTYPE html>
<html lang="nl">
<head>
<meta charset="utf-8">
<title>Volthaven flyer</title>
<link href="https://fonts.googleapis.com/css2?family=Montserrat:wght@300;400;500;600;700;800&family=Oswald:wght@500&display=swap" rel="stylesheet">
<style>
:root{
  --green:#7dbb1c;
  --green-bright:#8cc63f;
  --navy:#363a4b;
  --ink:#222530;
  --grey-text:#555a66;
  --paper:#ffffff;
  --backdrop:#5c5c5e;
}
*{box-sizing:border-box;margin:0;padding:0}
html,body{width:1200px;height:900px;overflow:hidden;background:var(--backdrop);font-family:"Montserrat",sans-serif}
.sheet{position:absolute;top:99px;width:495px;height:702px;background:var(--paper);overflow:hidden}
.sheet--front{left:78px}
.sheet--back{left:627px;background:linear-gradient(135deg,#ececed 0%,#fafafa 40%,#f4f4f5 100%)}
.abs{position:absolute}

/* front header */
.header-shape{left:0;top:0;width:495px;height:103px}
.brand{left:40px;top:28px;display:flex;align-items:center;gap:10px}
.brand__dot{width:40px;height:40px;border-radius:50%;background:var(--navy)}
.brand__name{font-weight:700;font-size:25px;color:var(--green);letter-spacing:.5px;line-height:1}
.brand__tag{font-size:9px;letter-spacing:2.6px;color:var(--navy);margin-top:5px}
.contact-top{left:345px;top:34px;color:#fff;font-weight:600;font-size:13.5px;line-height:24px}
.contact-top span{display:flex;align-items:center;gap:5px}
.contact-top b{font-weight:700;font-size:14px}

.hero{left:0;top:103px;width:495px;height:254px;background:radial-gradient(ellipse at 50% 20%,#8b98a3 0%,#3b4650 35%,#141a20 70%,#07090b 100%)}
.headline{left:0;top:186px;width:495px;text-align:center;color:#fff;font-size:33.5px;line-height:39px;font-weight:800;letter-spacing:.3px;white-space:nowrap}
.headline .thin{font-weight:300}
.headline .hl{color:var(--green-bright)}
.slogan{left:33px;top:313px;width:430px;height:22px;background:var(--green);color:#fff;font-weight:700;font-size:11.5px;text-align:center;line-height:22px;white-space:nowrap}

.adv-band{left:0;top:357px;width:495px;height:36px;background:var(--navy);color:#fff;font-size:19.5px;font-weight:300;text-align:center;line-height:36px;letter-spacing:.2px;white-space:nowrap}
.adv-band b{color:var(--green-bright);font-weight:700}
.adv-bg{left:0;top:393px;width:495px;height:240px;background:linear-gradient(160deg,#f6f6f6,#fff 60%)}
.adv{display:flex;align-items:center}
.adv svg{width:30px;height:30px;flex:none}
.adv__rule{width:1px;height:30px;background:var(--green);margin:0 8px 0 6px}
.adv__text{font-size:12px;font-weight:500;color:var(--ink);line-height:14.5px;white-space:nowrap}
.motor{left:336px;top:402px;width:126px;height:177px;background:radial-gradient(ellipse at center,#c9cbcd 0%,#8d9094 55%,#e9e9ea 100%);border-radius:8px}

.footer-front{left:0;top:633px;width:495px;height:69px;background:var(--navy)}
.photo{top:588px;width:103px;height:78px;border:2px solid #fff}
.photo--a{left:29px;background:linear-gradient(180deg,#a7b4bd 0%,#51606a 55%,#2e3b44 100%)}
.photo--b{left:140px;background:linear-gradient(180deg,#c5ccd2 0%,#6c7780 55%,#334049 100%)}
.photo--c{left:252px;background:linear-gradient(180deg,#8a9198 0%,#48525a 55%,#6f6b5a 100%)}
.photo--d{left:363px;background:linear-gradient(180deg,#b8c7d4 0%,#7f8f7a 50%,#3f5160 100%)}
.footer-line{left:0;top:674px;width:495px;text-align:center;color:#fff;font-size:11px;font-weight:400;display:flex;justify-content:center;align-items:center;gap:6px;white-space:nowrap}
.footer-line .sep{margin:0 8px}

/* back */
.title-bar{left:31px;width:432px;background:var(--navy);color:var(--green-bright);text-align:center;white-space:nowrap;overflow:hidden}
.title-bar--process{top:31px;height:37px;font-family:"Oswald",sans-serif;font-weight:500;font-size:18px;line-height:37px}
.title-bar--price{top:309px;height:33px;font-weight:700;font-size:21px;line-height:33px;letter-spacing:.3px}
.intro{left:0;width:495px;text-align:center;color:var(--ink);font-weight:400;white-space:nowrap}
.intro--process{top:76px;font-size:9.5px}
.intro--price{top:351px;font-size:12px;line-height:17px}
.steps{left:0;top:0;width:495px;height:300px}
.step-label{width:130px;text-align:center;font-size:10.2px;font-weight:600;color:var(--ink);line-height:13px;white-space:nowrap}

.card{top:393px;width:102px;height:259px;border:1.5px solid var(--navy);border-radius:4px;background:#fff;overflow:hidden}
.card__boat{height:54px;display:flex;align-items:center;justify-content:center}
.card__head{background:var(--navy);height:48px;color:#fff;text-align:center;padding-top:3px}
.card__name{font-size:12.5px;font-weight:700;line-height:13px}
.card__size{font-size:7.6px;font-weight:300;line-height:8.5px;margin-top:1px;white-space:nowrap}
.card__price{position:absolute;left:13px;top:90px;width:76px;height:24px;background:var(--green);color:#fff;text-align:center}
.card__price small{display:block;font-size:6px;line-height:7px;font-weight:300;color:#dcefc0}
.card__price b{display:block;font-size:12px;line-height:15px;font-weight:600}
.card__price--ask b{font-size:8.5px;line-height:24px;font-weight:700}
.card__list{list-style:none;padding-top:20px;text-align:center;color:var(--grey-text);font-size:8px;font-weight:400;line-height:10.5px;white-space:nowrap;letter-spacing:-.1px}
.card__list li{margin-bottom:5px}

.footer-back{left:0;top:667px;width:495px;height:35px;background:var(--navy);color:#fff;font-size:12.5px;font-weight:300;display:flex;align-items:center;justify-content:center;gap:22px;white-space:nowrap}
.footer-back span{display:flex;align-items:center;gap:5px}
</style>
</head>
<body>

<section class="sheet sheet--front">
  <svg class="abs header-shape" viewBox="0 0 495 103" aria-hidden="true">
    <polygon points="318,40 345,40 300,103 285,103" fill="var(--navy)"/>
    <polygon points="339,0 495,0 495,103 297,103" fill="var(--green)"/>
  </svg>
  <div class="abs brand">
    <div class="brand__dot"></div>
    <div>
      <div class="brand__name">VOLTHAVEN</div>
      <div class="brand__tag">ELEKTRISCH VAREN</div>
    </div>
  </div>
  <div class="abs contact-top">
    <span><svg width="10" height="10" viewBox="0 0 10 10"><circle cx="5" cy="5" r="4.2" fill="none" stroke="#fff"/><path d="M1 5h8M5 1c-2 2.5-2 5.5 0 8M5 1c2 2.5 2 5.5 0 8" fill="none" stroke="#fff" stroke-width=".7"/></svg>www.volthaven.nl</span>
    <span><svg width="10" height="10" viewBox="0 0 10 10"><circle cx="5" cy="5" r="4.2" fill="none" stroke="#fff"/><path d="M3.3 2.8l1 1-.6.6c.4.8 1 1.4 1.8 1.8l.6-.6 1 1-.8.8C4.6 7 3 5.4 2.5 3.6z" fill="#fff"/></svg><b>+31 6 12 345 678</b></span>
  </div>

  <div class="abs hero" role="img" aria-label="Photo of two electric outboard motors churning up white water"></div>
  <h1 class="abs headline">REBUILD <span class="thin">YOUR</span> <span class="hl">BOAT</span><br><span class="thin">INTO AN</span> <span class="hl">ELECTRICALLY</span><br>PROPELLED BOAT</h1>
  <div class="abs slogan">WE ARE THE BEST, NOT THE CHEAPEST, NOT THE MOST EXPENSIVE.</div>

  <div class="abs adv-band">ADVANTAGES OF <b>ELECTRIC BOATING ARE:</b></div>
  <div class="abs adv-bg"></div>

  <div class="abs adv" style="left:30px;top:413px">
    <svg viewBox="0 0 30 30" fill="none" stroke="var(--green)" stroke-width="1.5"><path d="M3 11h5l7-6v20l-7-6H3z"/><path d="M19 11c2 2 2 6 0 8M22 8c4 4 4 10 0 14M25 5c5 6 5 14 0 20"/></svg>
    <div class="adv__rule"></div><div class="adv__text">Completely<br>Silent</div>
  </div>
  <div class="abs adv" style="left:30px;top:476px">
    <svg viewBox="0 0 30 30" fill="none" stroke="var(--green)" stroke-width="1.5"><rect x="3" y="6" width="24" height="12" rx="1"/><circle cx="15" cy="12" r="3.5"/><path d="M8 21h14M10 24h10M15 18v9l-2-2M15 27l2-2"/></svg>
    <div class="adv__rule"></div><div class="adv__text">Cheap<br>To Operate</div>
  </div>
  <div class="abs adv" style="left:30px;top:540px">
    <svg viewBox="0 0 30 30" fill="none" stroke="var(--green)" stroke-width="1.5"><path d="M2 18h26l-4 5H6z"/><path d="M9 18v-4h9l3 4M12 14v-3h4"/></svg>
    <div class="adv__rule"></div><div class="adv__text">More<br>Enjoyable</div>
  </div>
  <div class="abs adv" style="left:168px;top:413px">
    <svg viewBox="0 0 30 30" fill="none" stroke="var(--green)" stroke-width="1.5"><circle cx="15" cy="15" r="12"/><circle cx="15" cy="15" r="7.5"/><circle cx="15" cy="15" r="3"/><path d="M3 15h24M15 3v24M15 15l8-8"/></svg>
    <div class="adv__rule"></div><div class="adv__text">Obliged In More<br>And More Areas</div>
  </div>
  <div class="abs adv" style="left:168px;top:453px">
    <svg viewBox="0 0 30 30" fill="none" stroke="var(--green)" stroke-width="1.5"><path d="M5 25l12-12M9 5a5 5 0 0 0 6 6M21 27l-6-6 3-3 6 6zM25 4l-16 16-4 1 1-4 16-16z"/></svg>
    <div class="adv__rule"></div><div class="adv__text">No Maintenance</div>
  </div>
  <div class="abs adv" style="left:168px;top:492px">
    <svg viewBox="0 0 30 30" fill="none" stroke="var(--green)" stroke-width="1.5"><rect x="4" y="17" width="17" height="6" rx="3"/><path d="M16 14c-2-3 2-4 0-8M20 13c-2-3 2-4 0-8M4 27L26 5"/></svg>
    <div class="adv__rule"></div><div class="adv__text">No Fumes, Smells<br>Or Smoke</div>
  </div>
  <div class="abs adv" style="left:168px;top:540px">
    <svg viewBox="0 0 30 30" fill="none" stroke="var(--green)" stroke-width="1.5"><path d="M15 4c5 4 5 10 0 14c-5-4-5-10 0-14zM15 18v-9M3 14l4 10h5M27 14l-4 10h-5"/></svg>
    <div class="adv__rule"></div><div class="adv__text">Environmentally<br>Friendly</div>
  </div>

  <div class="abs motor" role="img" aria-label="Technical wireframe drawing of an inboard electric motor"></div>

  <div class="abs footer-front"></div>
  <div class="abs photo photo--a" role="img" aria-label="Photo of a dark converted boat moored in a harbour"></div>
  <div class="abs photo photo--b" role="img" aria-label="Photo of people sailing a small electric boat in a marina"></div>
  <div class="abs photo photo--c" role="img" aria-label="Photo of a dark sloop reflected in calm water"></div>
  <div class="abs photo photo--d" role="img" aria-label="Photo of a small boat on a canal with city buildings behind"></div>
  <div class="abs footer-line">
    <svg width="8" height="10" viewBox="0 0 8 10"><path d="M4 9.5C1.5 6 1 5 1 4a3 3 0 0 1 6 0c0 1-.5 2-3 5.5z" fill="none" stroke="var(--green-bright)"/><circle cx="4" cy="4" r="1" fill="var(--green-bright)"/></svg>
    Havenkade 12,1000AB, Amsterdam (Noord), Nederland
    <span class="sep">|</span>
    <svg width="11" height="8" viewBox="0 0 11 8"><rect x=".5" y=".5" width="10" height="7" fill="none" stroke="var(--green-bright)"/><path d="M.5 .5l5 4 5-4" fill="none" stroke="var(--green-bright)"/></svg>
    info@volthaven.nl
  </div>
</section>

<section class="sheet sheet--back">
  <div class="abs title-bar title-bar--process">HOE WERKT HET ELEKTRISCH OMBOUWEN VAN EEN BOOT?</div>
  <p class="abs intro intro--process">HET OMBOUWEN VAN JOUW BOOT IS EEN PROJECT WAAR WIJ JE GRAAG BIJ BETREKKEN</p>

  <svg class="abs steps" viewBox="0 0 495 300" fill="none" aria-hidden="true">
    <g stroke="#8a8d94" stroke-width=".8" stroke-dasharray="2 1.5">
      <path d="M114 124H224M270 124H381M114 226H224M270 226H381"/>
      <path d="M427 124H450V226H427"/>
    </g>
    <g stroke="#8a8d94" stroke-width=".8" stroke-dasharray="1.5 1.5" fill="#fff">
      <circle cx="91" cy="124" r="23"/><circle cx="247" cy="124" r="23"/><circle cx="404" cy="124" r="23"/>
      <circle cx="91" cy="226" r="23"/><circle cx="247" cy="226" r="23"/><circle cx="404" cy="226" r="23"/>
    </g>
    <g stroke="var(--green)" stroke-width="1.4" stroke-linejoin="round" stroke-linecap="round">
      <path d="M79 116h18a3 3 0 0 1 3 3v6a3 3 0 0 1-3 3h-10l-5 4v-4h-3a3 3 0 0 1-3-3v-6a3 3 0 0 1 3-3z"/>
      <path d="M98 121h4a2 2 0 0 1 2 2v5a2 2 0 0 1-2 2h-1v3l-3-3"/>
      <circle cx="239" cy="130" r="5"/><circle cx="255" cy="130" r="5"/><path d="M236 126l3-11h3l2 8h6l2-8h3l3 11M244 123v-3h6v3"/>
      <path d="M394 134l18-18M397 114l3 3-3 3M411 134l-6-6 3-3 6 6M414 114l-14 14"/>
      <path d="M80 219h16l-2 14H80zM96 222h4v6h-4M89 220l-4 6h5l-3 6"/>
      <rect x="238" y="214" width="18" height="23" rx="1"/><path d="M243 212h8v4h-8zM241 228l3-4 3 3 3-5 3 6M241 232h12"/>
      <path d="M396 234c2-8 8-16 16-18-2 8-10 14-16 18zM400 226l-4-1 3-4 4 1M404 230l1 4 4-3-1-4M394 237l-3 4M398 238l-2 4"/>
    </g>
  </svg>
  <div class="abs step-label" style="left:26px;top:157px">KENNISMAKING</div>
  <div class="abs step-label" style="left:182px;top:157px">PLANNING EN START<br>VAN HET PROJECT</div>
  <div class="abs step-label" style="left:339px;top:157px">OUD ERUIT</div>
  <div class="abs step-label" style="left:26px;top:256px">VAREN<br>EN SERVICE</div>
  <div class="abs step-label" style="left:182px;top:256px">TEST &amp;<br>OVERDRACHT</div>
  <div class="abs step-label" style="left:339px;top:256px">NIEUW<br>ERIN</div>

  <div class="abs title-bar title-bar--price">PRIJZEN VOOR HET OMBOUWEN</div>
  <p class="abs intro intro--price">RICHTPRIJZEN VAN ONZE STANDAARD PAKKETTEN WAARMEE U<br>MINIMAAL 8 UUR KUNT VAREN.</p>

  <div class="abs card" style="left:34px">
    <div class="card__boat"><svg width="76" height="30" viewBox="0 0 76 30" fill="none" stroke="var(--ink)" stroke-width="1.3"><path d="M2 8h72l-4 10c-20 4-45 5-66 4z"/><rect x="7" y="11" width="9" height="6"/><path d="M4 24h12"/></svg></div>
    <div class="card__head"><div class="card__name">KLEIN</div><div class="card__size">tot 5 mtr</div></div>
    <div class="card__price"><small>vanaf</small><b>€2200</b></div>
    <ul class="card__list"><li>Outboard</li><li>1,1kW motor (4pk)</li><li>915 Wh Li-Ion</li><li>GPS tracker</li><li>Draagbare accu</li><li>zelf te monteren</li><li>perfecte<br>vervaning voor<br>buitenboordmotor</li></ul>
  </div>
  <div class="abs card" style="left:142px">
    <div class="card__boat"><svg width="76" height="30" viewBox="0 0 76 30" fill="none" stroke="var(--ink)" stroke-width="1.3"><path d="M2 8h72l-4 10c-20 4-45 5-66 4z"/><rect x="7" y="11" width="11" height="6"/><path d="M4 24h12"/></svg></div>
    <div class="card__head"><div class="card__name">MIDDEL</div><div class="card__size">5 mtr tot 8,5 mtr</div></div>
    <div class="card__price"><small>vanaf</small><b>€12500</b></div>
    <ul class="card__list"><li>Inboard</li><li>8,5kW | 81Nm | 35pk*1</li><li>12kW accupakket</li><li>inclusief inbouw</li><li>Inclusief lader</li><li>Zuinig &amp; Krachtig</li><li>IP 67 waterproof</li></ul>
  </div>
  <div class="abs card" style="left:250px">
    <div class="card__boat"><svg width="76" height="30" viewBox="0 0 76 30" fill="none" stroke="var(--ink)" stroke-width="1.3"><path d="M2 8h72l-4 10c-20 4-45 5-66 4z"/><rect x="7" y="11" width="13" height="6"/><path d="M4 24h12"/></svg></div>
    <div class="card__head"><div class="card__name">GROOT</div><div class="card__size">7 mtr tot 10 mtr</div></div>
    <div class="card__price"><small>vanaf</small><b>€17500</b></div>
    <ul class="card__list"><li>Inboard</li><li>17,5kW | 209Nm | 55pk*1</li><li>20kW accupakket</li><li>inclusief inbouw</li><li>Inclusief lader</li><li>Zuinig &amp; Krachtig</li><li>IP 67 waterproof</li></ul>
  </div>
  <div class="abs card" style="left:358px">
    <div class="card__boat"><svg width="76" height="30" viewBox="0 0 76 30" fill="none" stroke="var(--ink)" stroke-width="1.3"><path d="M2 8h72l-4 10c-20 4-45 5-66 4z"/><rect x="7" y="11" width="12" height="6"/><rect x="20" y="11" width="12" height="6"/><rect x="33" y="11" width="12" height="6"/><path d="M4 24h12"/></svg></div>
    <div class="card__head"><div class="card__name">ANDERS</div><div class="card__size">vanaf 10 meter of<br>snelvarend</div></div>
    <div class="card__price card__price--ask"><b>OP AANVRAAG</b></div>
    <ul class="card__list"><li>Inboard en Outboard</li><li>Maatwerk</li><li>Elke Capaciteit</li><li>Inbouw op maat</li><li>Laag,- en<br>hoogspanning</li><li>Ook voor advies</li><li>Partnernetwerk</li></ul>
  </div>

  <div class="abs footer-back">
    <span><svg width="10" height="10" viewBox="0 0 10 10"><circle cx="5" cy="5" r="4.2" fill="none" stroke="var(--green-bright)"/><path d="M1 5h8M5 1c-2 2.5-2 5.5 0 8M5 1c2 2.5 2 5.5 0 8" fill="none" stroke="var(--green-bright)" stroke-width=".7"/></svg>www.volthaven.nl</span>
    <span>|</span>
    <span><svg width="10" height="10" viewBox="0 0 10 10"><circle cx="5" cy="5" r="4.2" fill="none" stroke="var(--green-bright)"/><path d="M3.3 2.8l1 1-.6.6c.4.8 1 1.4 1.8 1.8l.6-.6 1 1-.8.8C4.6 7 3 5.4 2.5 3.6z" fill="var(--green-bright)"/></svg>+31 6 12 345 678</span>
    <span>|</span>
    <span><svg width="11" height="8" viewBox="0 0 11 8"><rect x=".5" y=".5" width="10" height="7" fill="none" stroke="var(--green-bright)"/><path d="M.5 .5l5 4 5-4" fill="none" stroke="var(--green-bright)"/></svg>info@volthaven.nl</span>
  </div>
</section>

</body>
</html>
```